The Harlow Reserve Web Site design

I need a web design for my luxury range of Terry Toweling and Spa Accessories for luxury upmarket hotels and Spas. I have a catalog that sets the mood and tone I am looking for. I need a website design that shows off the look and feel of this luxury range while working back to the catalog look and feel. Its all about Upmarket and Luxury. I will be using the website as a reference site and as a site that customers can purchase off.
The Logo is attached as is the catalog. I don't mind changing the color of the Logo to match the website. However I would prefer to keep the font of that logo.

http://thegallerydesk.pixvault-example.com/p504729381
Please can you try and access this link. The Harlow Reserve
Name Greta. Email greta@vellumsupply-example.com.au. Password Harlow.
These images are to be used for shopping page and please use the close up details of texture as background on pages and use those texture details and close ups for banners

Please note the look and feel has to be very upmarket and super luxury. Ficus is on mood and not on retail.
Have a look at the mood on the following websites
Www.gracefulretreats-example.com
And yourcosyseasidecabin-example.com
That one is retail .mi don't want retail focus but it's very clean. And simple and colors are good
Updates

Please rebook brief. I have added some important detail. Thanks

Relook brief. I have added,important detail. Thanks

Target Market(s)

Corporate buyers
This is not for retail selling to consumers
Price it's viewed only after secure login

Industry/Entity Type

Shopping

Colors
acd037
cadf82
fbc995
fce7d3
faa54b

Requirements
Must have
• Luxury. Think luxury. Very high end yet modern like the catalogue
Use banners on home page
Should not have
• Don't use the blue as the main color. It's too cheap.
No products on home page

```html
<!DOCTYPE html>
<html lang="en">
<head>
<meta charset="utf-8">
<title>The Harlow Reserve</title>
<link rel="stylesheet" href="https://fonts.googleapis.com/css2?family=Ubuntu:wght@400;500;700&family=Oxygen:wght@400&family=Libre+Baskerville:wght@700&display=swap">
<style>
:root{
  --green:#acd037;
  --green-soft:#cadf82;
  --green-nav:#8aa829;
  --green-deep:#5e7818;
  --olive-dark:#3f5010;
  --peach:#faa54b;
  --peach-soft:#fbc995;
  --cream:#fce7d3;
  --grey-nav:#5b5b5b;
  --ink:#2a2a2a;
  --text:#3d3d3d;
  --line:#d9d9d9;
  --footer-top:#faf4ec;
  --footer-bottom:#f1e6d8;
  --paper:#f7ecdc;
  --card-foot:#f6ede2;
  --white:#ffffff;
}
*{box-sizing:border-box;margin:0;padding:0}
html,body{width:1154px;height:1200px;overflow:hidden;background:var(--white)}
body{position:relative;font-family:"Ubuntu",sans-serif;color:var(--text)}
.abs{position:absolute}
a{color:inherit;text-decoration:none}

.side-arrow{top:282px;width:50px;height:72px}
.side-arrow.prev{left:56px}
.side-arrow.next{left:1048px}

.page{left:126px;top:0;width:903px;height:1022px;background:var(--white);box-shadow:0 0 8px rgba(0,0,0,.12)}

/* header */
.brand{left:147px;top:48px;font-family:"Oxygen",sans-serif;font-size:33px;color:var(--green-deep);letter-spacing:.3px}
.brand-art{left:525px;top:22px;width:136px;height:92px;border-radius:40px;background:linear-gradient(135deg,#cfe6a8 0%,#f6e2c8 50%,#f3d99a 100%)}
.account{left:663px;top:13px;font-size:12.5px;color:var(--green-deep);display:flex;align-items:center;gap:9px;white-space:nowrap}
.account .cart{display:flex;align-items:center;gap:5px}
.checkout{left:935px;top:8px;width:72px;height:26px;border-radius:13px;background:var(--green-deep);color:var(--white);font-size:12.5px;text-align:center;line-height:26px}
.search{left:838px;top:69px;width:168px;height:27px;border-radius:14px;background:linear-gradient(#fbfaf6,#efece4);border:1px solid #d8d3c6;font-size:13px;color:var(--green-deep);padding:6px 0 0 14px}
.search svg{position:absolute;right:10px;top:5px}

/* nav */
.nav{left:126px;top:129px;width:903px;height:35px;background:var(--green-nav);display:flex}
.nav a{color:var(--white);font-size:16px;line-height:35px;text-align:center;border-right:1px solid rgba(255,255,255,.3)}
.nav a.current{background:var(--grey-nav)}
.nav a:last-child{border-right:0}

/* hero */
.hero{left:126px;top:165px;width:903px;height:375px;background:linear-gradient(100deg,#efe2d6 0%,#f7f1ea 30%,#ebe7df 60%,#d8d3c9 100%)}
.hero-caption{left:126px;top:395px;width:610px;height:62px}
.hero-caption p{position:absolute;left:20px;top:6px;font-family:"Libre Baskerville",serif;font-weight:700;font-size:17.5px;line-height:27px;color:#1e1e1e;white-space:nowrap}

/* categories */
.card{top:477px;width:207px;height:194px;background:var(--white);box-shadow:0 2px 6px rgba(0,0,0,.18)}
.card .tab{position:absolute;left:3px;top:0;height:30px}
.card .tab span{position:absolute;left:10px;top:0;line-height:30px;color:var(--white);font-size:13px;font-weight:500;white-space:nowrap}
.card .art{position:absolute;left:3px;top:30px;width:201px;height:120px}
.card .foot{position:absolute;left:3px;top:150px;width:201px;height:42px;background:var(--card-foot);font-size:13px;font-weight:500;line-height:15px;color:var(--ink);padding:6px 0 0 9px}
.card .foot svg{position:absolute;right:8px;top:11px}

/* get started */
.get{left:144px;top:687px;width:864px;height:59px;background:var(--green-nav)}
.get svg{position:absolute;left:0;top:0}
.get h2{position:absolute;left:12px;top:9px;font-size:36px;font-weight:400;color:var(--white);letter-spacing:.5px}
.get h2 b{font-weight:700}
.get p{position:absolute;left:243px;top:10px;width:610px;font-size:12.5px;line-height:20px;color:var(--white)}

/* welcome */
.welcome{left:144px;top:770px;width:640px}
.welcome h1,.offers h2{font-size:20px;font-weight:400;color:var(--ink)}
.welcome h1 span,.offers h2 span{color:var(--green-deep)}
.welcome p{font-size:12.4px;line-height:18.8px;color:var(--text);margin-top:6px;text-align:justify}
.welcome p+p{margin-top:8px}
.read-more{left:698px;top:972px;width:75px;height:23px;background:#1c1c1c;color:var(--white);font-size:12px;text-align:center;line-height:23px;border-radius:2px}

/* seasonal feature */
.offers{left:806px;top:770px;width:201px}
.offer-art{left:806px;top:804px;width:201px;height:114px;background:linear-gradient(160deg,var(--cream) 0%,var(--peach-soft) 45%,var(--peach) 100%)}
.offer-title{left:806px;top:922px;width:201px;font-size:15px;line-height:20px;font-weight:500;color:var(--green-deep)}
.offer-rule{left:806px;top:965px;width:201px;height:1px;background:var(--line)}
.view{left:806px;top:975px;width:201px;font-size:14px;color:var(--green-deep);display:flex;align-items:center;justify-content:flex-end;gap:8px}

/* footer */
.footer{left:0;top:1022px;width:1154px;height:178px;background:linear-gradient(var(--footer-top),var(--footer-bottom));border-top:1px solid #e2d6c6}
.foot-links{left:127px;top:1038px;font-size:12.5px;color:var(--text)}
.foot-links .sep{margin:0 5px}
.social{top:1030px;display:flex;align-items:flex-end;gap:6px;font-size:12px;color:var(--ink)}
.social i{display:block;width:20px;height:22px;background:#1a1a1a}
.foot-rule{left:127px;top:1064px;width:657px;height:1px;background:#dccfbd}
.col-title{top:1075px;font-size:14.5px;font-weight:700;color:var(--green-deep)}
.vline{top:1072px;width:1px;height:86px;background:#dccfbd}
.email-field{left:129px;top:1112px;width:172px;height:26px;background:var(--white);border:1px solid #d6d6d6;font-size:11px;font-style:italic;color:#555;padding:6px 0 0 8px}
.email-go{left:308px;top:1112px;width:30px;height:26px;background:var(--white);border:1px solid #d6d6d6}
.email-go svg{position:absolute;left:8px;top:6px}
.contact-line{left:393px;font-size:12px;color:var(--text);display:flex;align-items:center;gap:10px}
.dashes{left:393px;width:200px;border-top:1px dotted #cbbfae}
.pay{top:1113px;width:37px;height:24px;background:var(--white);border:1px solid #cbbfae;border-radius:3px;font-size:7.5px;font-weight:500;color:var(--olive-dark);display:flex;align-items:center;justify-content:center;letter-spacing:-.1px}
.copy{left:360px;top:1174px;font-size:12px;color:var(--olive-dark)}

.note{left:812px;top:1030px;width:196px;height:158px;background:var(--paper);transform:rotate(-2deg);box-shadow:2px 3px 6px rgba(0,0,0,.22);text-align:center}
.note h3{margin-top:22px;font-size:16px;font-weight:700;color:var(--olive-dark)}
.note p{margin:6px auto 0;width:150px;font-size:11.5px;line-height:19px;color:var(--ink)}
.note .q{color:var(--peach);font-weight:700}
.note .who{margin-top:2px;font-size:12px;font-weight:700;color:var(--ink)}
.note .dots{display:flex;justify-content:center;gap:3px;margin-top:8px}
.note .dots i{width:7px;height:7px;background:#4a4a4a}
.note .dots i:first-child{background:var(--green-nav)}
.clip{left:820px;top:1010px}
</style>
</head>
<body>

<svg class="abs side-arrow prev" viewBox="0 0 50 72" aria-hidden="true"><path d="M48 0 C30 14 30 58 48 72" fill="none" stroke="#e6e6e6" stroke-width="3"/><path d="M22 27 L14 36 L22 45" fill="none" stroke="#111" stroke-width="4"/></svg>
<svg class="abs side-arrow next" viewBox="0 0 50 72" aria-hidden="true"><path d="M2 0 C20 14 20 58 2 72" fill="none" stroke="#e6e6e6" stroke-width="3"/><path d="M28 27 L36 36 L28 45" fill="none" stroke="#111" stroke-width="4"/></svg>

<div class="abs page"></div>

<div class="abs brand">The Harlow Reserve</div>
<div class="abs brand-art" role="img" aria-label="Rolled soft green, cream and peach towels"></div>
<div class="abs account">
  <a href="#">Login</a><span>|</span>
  <a href="#">Create An Account</a><span>|</span>
  <a href="#" class="cart"><svg width="16" height="14" viewBox="0 0 16 14"><path d="M1 1h3l2 8h8l1.5-6H5" fill="none" stroke="#5e7818" stroke-width="1.6"/><circle cx="7" cy="12" r="1.4" fill="#5e7818"/><circle cx="13" cy="12" r="1.4" fill="#5e7818"/></svg>0 Items</a><span>|</span>
</div>
<a href="#" class="abs checkout">Check Out</a>
<div class="abs search">Search<svg width="18" height="18" viewBox="0 0 18 18"><circle cx="7.5" cy="7.5" r="5.5" fill="none" stroke="#3f5010" stroke-width="2"/><path d="M11.5 11.5 L16 16" stroke="#3f5010" stroke-width="2.4"/></svg></div>

<nav class="abs nav">
  <a href="#" class="current" style="width:99px">Home</a>
  <a href="#" style="width:125px">About Us</a>
  <a href="#" style="width:145px">Our Products</a>
  <a href="#" style="width:147px">Latest News</a>
  <a href="#" style="width:104px">FAQ's</a>
  <a href="#" style="width:150px">Testimonials</a>
  <a href="#" style="width:133px">Contact Us</a>
</nav>

<div class="abs hero" role="img" aria-label="Spa scene with stacked white towels, white orchids and soft candlelight"></div>
<div class="abs hero-caption">
  <svg width="610" height="62" viewBox="0 0 610 62" style="position:absolute;left:0;top:0" aria-hidden="true"><path d="M0 0 H576 L610 62 H0 Z" fill="#ffffff" fill-opacity=".72"/></svg>
  <p>Lorem ipsum dolor sit amet, consectetuer adipiscing eliert,<br>sed diam nonummy nibh euismod tincidunt ut laoreet.</p>
</div>

<div class="abs card" style="left:144px">
  <svg class="tab" width="150" height="30" viewBox="0 0 150 30" aria-hidden="true"><path d="M0 0 H130 L150 30 H0Z" fill="#8aa829"/><path d="M0 0 V30" stroke="#faa54b" stroke-width="4"/></svg>
  <div class="tab"><span>Health &amp; Beauty</span></div>
  <div class="art" role="img" aria-label="Colourful rolled towels with a flower" style="background:linear-gradient(135deg,#f3c54a,#3fa7d8 50%,#7dbb3b)"></div>
  <div class="foot">Lorem ipsum dolor sita,<br>consectetuer.<svg width="20" height="20" viewBox="0 0 20 20"><circle cx="10" cy="10" r="10" fill="#3f5010"/><path d="M5 10h9M10 6l4 4-4 4" fill="none" stroke="#fff" stroke-width="2"/></svg></div>
</div>
<div class="abs card" style="left:363px">
  <svg class="tab" width="130" height="30" viewBox="0 0 130 30" aria-hidden="true"><path d="M0 0 H110 L130 30 H0Z" fill="#8aa829"/></svg>
  <div class="tab"><span>Hair Dressing</span></div>
  <div class="art" role="img" aria-label="Person wearing a pink hair towel wrap" style="background:linear-gradient(90deg,#f2e6e2,#e9b9c3 60%,#f4eeec)"></div>
  <div class="foot">Lorem ipsum dolor sita,<br>consectetuer.<svg width="20" height="20" viewBox="0 0 20 20"><circle cx="10" cy="10" r="10" fill="#3f5010"/><path d="M5 10h9M10 6l4 4-4 4" fill="none" stroke="#fff" stroke-width="2"/></svg></div>
</div>
<div class="abs card" style="left:581px">
  <svg class="tab" width="130" height="30" viewBox="0 0 130 30" aria-hidden="true"><path d="M0 0 H110 L130 30 H0Z" fill="#8aa829"/></svg>
  <div class="tab"><span>Health Care</span></div>
  <div class="art" role="img" aria-label="Stack of blue and pink towels with a flower" style="background:linear-gradient(180deg,#f4f4f4 0%,#3cb4e6 35%,#e25aa8 100%)"></div>
  <div class="foot">Lorem ipsum dolor sita,<br>consectetuer.<svg width="20" height="20" viewBox="0 0 20 20"><circle cx="10" cy="10" r="10" fill="#3f5010"/><path d="M5 10h9M10 6l4 4-4 4" fill="none" stroke="#fff" stroke-width="2"/></svg></div>
</div>
<div class="abs card" style="left:800px">
  <svg class="tab" width="130" height="30" viewBox="0 0 130 30" aria-hidden="true"><path d="M0 0 H110 L130 30 H0Z" fill="#8aa829"/></svg>
  <div class="tab"><span>Leisure</span></div>
  <div class="art" role="img" aria-label="Rolled cream towels with a seashell" style="background:linear-gradient(135deg,#fbf4e2,#eed79f 55%,#f6f2ea)"></div>
  <div class="foot">Lorem ipsum dolor sita,<br>consectetuer.<svg width="20" height="20" viewBox="0 0 20 20"><circle cx="10" cy="10" r="10" fill="#3f5010"/><path d="M5 10h9M10 6l4 4-4 4" fill="none" stroke="#fff" stroke-width="2"/></svg></div>
</div>

<div class="abs get">
  <svg width="230" height="59" viewBox="0 0 230 59" aria-hidden="true"><path d="M0 0 H215 L230 29.5 L215 59 H0Z" fill="#3f5010"/></svg>
  <h2><b>GET</b> Started</h2>
  <p>Lorem ipsum dolor sit amet, consectetuer adipiscing elit, sed diam nonummy nibh euismod tincidunt ut laoreet dolore magna aliquam erat volutpat. Ut wisi enim ad minim veniam, quis nostrud exerci ta.</p>
</div>

<section class="abs welcome">
  <h1>Welcome to <span>HarlowCollection</span></h1>
  <p>Lorem ipsum dolor sit amet, consectetuer adipiscing elit, sed diam nonummy nibh euismod tincidunt ut laoreet dolore magna aliquam erat volutpat. Ut wisi enim ad minim veniam, quis nostrud exerci tation ullamcorper suscipit lobortis nisl ut aliquip ex ea commodo consequat. Duis autem vel eum iriure dolor in hendrerit in vulputate velit esse molestie consequat, vel illum dolore eu feugiat nulla.</p>
  <p>Lorem ipsum dolor sit amet, consectetuer adipiscing elit, sed diam nonummy nibh euismod tincidunt ut laoreet dolore magna aliquam erat volutpat. Ut wisi enim ad minim veniam, quis nostrud exerci tation ullamcorper suscipit lobortis nisl ut aliquip ex ea commodo consequat. Duis autem vel eum iriure dolor in hendrerit in vulputate velit esse molestie consequat, vel illum dolore eu feugiat nulla facilisis at vero eros et ing.</p>
</section>
<a href="#" class="abs read-more">Read More</a>

<section class="abs offers"><h2>Special <span>Collections</span></h2></section>
<div class="abs offer-art" role="img" aria-label="Close-up of soft peach terry towel texture"></div>
<div class="abs offer-title">Signature Spa Range in Peach or Blush</div>
<div class="abs offer-rule"></div>
<a href="#" class="abs view">Explore the Range<svg width="8" height="10" viewBox="0 0 8 10"><path d="M0 0 L8 5 L0 10Z" fill="#5e7818"/></svg></a>

<footer class="abs footer"></footer>
<div class="abs foot-links">Home<span class="sep">|</span>About Us<span class="sep">|</span>Our Products<span class="sep">|</span>Latest News<span class="sep">|</span>FAQ's<span class="sep">|</span>Testimonials<span class="sep">|</span>Contact Us</div>
<div class="abs social" style="left:640px"><i></i>Friendsly</div>
<div class="abs social" style="left:724px"><i></i>Chirpnet</div>
<div class="abs foot-rule"></div>

<div class="abs col-title" style="left:129px">Subscribe to Newsletter</div>
<div class="abs email-field">Email here</div>
<div class="abs email-go"><svg width="14" height="14" viewBox="0 0 14 14"><path d="M3 1 L10 7 L3 13" fill="none" stroke="#5e7818" stroke-width="3"/></svg></div>

<div class="abs vline" style="left:362px"></div>
<div class="abs col-title" style="left:393px">Contact Us</div>
<div class="abs dashes" style="top:1098px"></div>
<div class="abs contact-line" style="top:1102px"><svg width="12" height="12" viewBox="0 0 12 12"><path d="M2 1 L4.5 1 L5.5 3.5 L4 4.8 C4.8 6.6 5.6 7.4 7.2 8 L8.5 6.5 L11 7.5 L11 10 C11 10.6 10.5 11 10 11 C5 11 1 7 1 2 C1 1.5 1.4 1 2 1Z" fill="#666"/></svg>012-555-0199</div>
<div class="abs dashes" style="top:1122px"></div>
<div class="abs contact-line" style="top:1126px"><svg width="13" height="10" viewBox="0 0 13 10"><rect width="13" height="10" fill="#666"/><path d="M0 0 L6.5 5.5 L13 0" fill="none" stroke="#eee" stroke-width="1.2"/></svg>info@ harlowcollection.com</div>
<div class="abs dashes" style="top:1146px"></div>

<div class="abs vline" style="left:612px"></div>
<div class="abs col-title" style="left:626px">We Accept</div>
<div class="abs pay" style="left:626px">Paycard</div>
<div class="abs pay" style="left:667px">Duocard</div>
<div class="abs pay" style="left:708px">Sendwell</div>
<div class="abs pay" style="left:749px">Cloudbank</div>

<div class="abs copy">© 2014 &nbsp;Harlowcollection. All Rights Reserved.</div>

<div class="abs note">
  <h3>Client Testimonials</h3>
  <p><span class="q">“</span> Lorerem ipsum dolor sit amereeret, consectetuer adipiscing elt <span class="q">”</span></p>
  <div class="who">Client Name</div>
  <div class="dots"><i></i><i></i><i></i></div>
</div>
<svg class="abs clip" width="26" height="32" viewBox="0 0 26 32" aria-hidden="true"><path d="M8 30 C2 22 4 6 12 4 C20 2 22 12 16 16 C12 18 9 14 12 11" fill="none" stroke="#5e7818" stroke-width="2"/></svg>

</body>
</html>
```